Copperleaf Venture Trust

Take current power point presentation and make it uniform in color and font, and create designs that pop throughout the presentation. Right now, it is dull and mundane.

```html
<!DOCTYPE html>
<html lang="en">
<head>
<meta charset="utf-8">
<title>Copperleaf Venture Trust – Presentation</title>
<link href="https://fonts.googleapis.com/css2?family=Poppins:wght@400;500;600;700&display=swap" rel="stylesheet">
<style>
:root{
  --blue:#0d6cb8;
  --blue-dark:#0b2e52;
  --ink:#1c1c1c;
  --text:#3a3a3a;
  --muted:#6d6d6d;
  --page:#ffffff;
  --footer-tag:#111111;
}
*{box-sizing:border-box;margin:0;padding:0}
html,body{width:1200px;height:835px;overflow:hidden;background:var(--page)}
body{position:relative;font-family:'Poppins',sans-serif;color:var(--ink)}

.slide{position:absolute;width:670px;height:377px;background:#fff;overflow:hidden;
  transform:scale(.5239);transform-origin:0 0;box-shadow:0 6px 26px rgba(0,0,0,.16)}
.col-1{left:33.5px}.col-2{left:426px}.col-3{left:818.3px}
.row-1{top:52px}.row-2{top:314.3px}.row-3{top:576.8px}

.slide-title{position:absolute;left:0;top:12px;padding-left:14px;border-left:3px solid var(--blue);
  font-size:19px;font-weight:600;line-height:24px;color:var(--ink)}
.brand{position:absolute;right:12px;top:14px;display:flex;align-items:center;gap:5px;
  font-size:9px;font-weight:600;color:var(--blue);white-space:nowrap}
.brand i{width:9px;height:9px;background:var(--blue);display:block}
.footer{position:absolute;left:0;bottom:8px;width:620px;height:21px;background:var(--blue);
  color:#fff;font-size:7px;line-height:21px;padding-left:10px}
.page-no{position:absolute;right:0;bottom:8px;width:44px;height:21px;background:var(--footer-tag);
  color:#fff;font-size:7px;font-weight:500;line-height:21px;text-align:center}

.ring-list{list-style:none}
.ring-list li{position:relative;padding-left:12px;font-size:8.4px;line-height:15px;color:var(--text)}
.ring-list li::before{content:"";position:absolute;left:0;top:5px;width:5px;height:5px;border:1px solid var(--blue);border-radius:50%}
.dot-list{list-style:none}
.dot-list li{position:relative;padding-left:16px;font-size:10.5px;line-height:19.5px;color:var(--ink)}
.dot-list li::before{content:"";position:absolute;left:2px;top:7px;width:5px;height:5px;background:var(--blue);border-radius:50%}
.accent{color:var(--blue);font-weight:600}

.photo{position:absolute}
.photo-frame{position:absolute;border:1.5px solid var(--blue)}
.photo-block{position:absolute;background:var(--blue)}
.outlined-box{position:absolute;border:1.5px solid var(--blue);background:#fff}

/* cover */
.cover-photo{position:absolute;inset:0;background:radial-gradient(ellipse at 50% 45%,#234f7c 0%,#123456 55%,#081d33 100%)}
.cover-name{position:absolute;left:0;right:0;top:150px;text-align:center;color:#fff;font-size:40px;font-weight:600;line-height:46px}

/* agenda */
.agenda-col{position:absolute;top:78px}
.agenda-main{list-style:none}
.agenda-main>li{position:relative;padding-left:15px;font-size:12.5px;font-weight:600;line-height:37px;color:var(--ink)}
.agenda-main>li::before{content:"";position:absolute;left:0;top:15px;width:6px;height:6px;border:1.5px solid var(--blue);border-radius:50%}
.agenda-main .dot-list{margin-top:-8px;margin-left:0;font-weight:400}

/* strategy */
.box-heading{font-size:11px;font-weight:600;color:var(--ink);margin-bottom:6px}

/* org chart */
.chart-head{position:absolute;left:390px;top:75px;width:243px;height:53px;background:var(--blue);border-radius:3px;
  color:#fff;font-size:15.5px;font-weight:700;text-align:center;line-height:53px}
.chart-member{position:absolute;left:440px;width:193px;height:37px;border:1px solid #2a2a2a;border-radius:3px;
  font-size:10px;font-weight:600;text-align:center;line-height:35px;background:#fff}

/* team */
.person-photo{position:absolute;left:9px;width:71px;height:83px;border-bottom:3px solid var(--blue);
  background:linear-gradient(160deg,#9a9a9a,#3c3c3c)}
.person{position:absolute;left:89px;right:14px}
.person h3{font-size:11.5px;font-weight:500;color:var(--ink);margin-bottom:4px}
.person .ring-list li{font-size:6.6px;line-height:10.6px}
.person .ring-list li::before{top:3px;width:4px;height:4px}

/* logo panel */
.brand-panel{position:absolute;left:838px;top:615px;width:306px;height:120px;display:flex;align-items:center;gap:14px}
.brand-panel i{display:block;width:26px;height:26px;background:var(--blue);flex:none}
.brand-panel span{font-size:33px;font-weight:600;line-height:38px;color:var(--blue)}
</style>
</head>
<body>

<!-- Cover -->
<section class="slide col-1 row-1">
  <div class="cover-photo" role="img" aria-label="Analyst seated before a wall of pinned charts, tinted deep blue"></div>
  <div class="cover-name">Copperleaf<br>Venture Trust</div>
</section>

<!-- Disclosure -->
<section class="slide col-2 row-1">
  <h2 class="slide-title">Disclosure</h2>
  <div class="brand"><i></i>Copperleaf Venture Trust</div>
  <ul class="ring-list" style="position:absolute;left:55px;top:62px;width:552px;text-align:justify">
    <li style="margin-bottom:9px">This Presentation is a summary and does not constitute an offer to sell, or a solicitation of any offer to buy or sell, any securities. Any such offer will be made solely to qualified investors by means of an offering memorandum and related subscription materials, which will contain material information not contained herein. This Presentation is not intended to replace any such offering memorandum.</li>
    <li style="margin-bottom:9px" class="accent"><span class="accent">No assurance can be given that the objectives discussed herein will be achieved and results may vary substantially on a quarterly, annual or other periodic basis. Past performance is not necessarily indicative of future results.</span></li>
    <li style="margin-bottom:9px">Prospective reviewers should not construe this Presentation, any offering memorandum or any other communication received from CVT or its affiliates as legal, accounting, tax, investment or other advice, and each reviewer should consult with its own counsel and advisors as to all legal, tax, regulatory, financial and related matters.</li>
    <li><span class="accent">This Presentation is confidential and proprietary to CVT.</span> Accordingly, this Presentation is to be treated as strictly confidential and not disclosed, directly or indirectly, to any party other than the person to whom it has been delivered and such person's professional advisors. Any distribution of this Presentation, in whole or in part, or the divulgence of any of its contents, is unauthorized. No person has been authorized to give any information or make any representations other than as set forth herein.</li>
  </ul>
  <div class="footer">© 2025. ALL Rights Reserved.</div><div class="page-no">Page 02</div>
</section>

<!-- Agenda -->
<section class="slide col-3 row-1">
  <h2 class="slide-title">Agenda</h2>
  <div class="brand"><i></i>Copperleaf Venture Trust</div>
  <div class="agenda-col" style="left:70px">
    <ul class="agenda-main">
      <li>Objectives</li>
      <li>Strategy</li>
      <li>The CVT organization
        <ul class="dot-list"><li>Senior Management</li><li>CVT's competitive advantage</li><li>How we are different</li></ul>
      </li>
    </ul>
  </div>
  <div class="agenda-col" style="left:316px">
    <ul class="agenda-main">
      <li>Performance</li>
      <li>Structure &amp; Terms</li>
      <li>Why Direct Investments?
        <ul class="dot-list"><li>Why CVT' Direct Invest Strategy?</li><li>Industry Overview</li><li>Differentiation Between PIPEs and Direct Investments</li><li>Capital/Deal Structure</li><li>Process</li><li>Protection/Risk</li></ul>
      </li>
    </ul>
  </div>
  <div class="footer">© 2025. ALL Rights Reserved.</div><div class="page-no">Page 03</div>
</section>

<!-- Objectives -->
<section class="slide col-1 row-2">
  <h2 class="slide-title">Objectives</h2>
  <div class="brand"><i></i>Copperleaf Venture Trust</div>
  <div class="photo-frame" style="left:16px;top:64px;width:184px;height:140px;border-bottom:none"></div>
  <div class="photo-block" style="left:226px;top:250px;width:84px;height:76px"></div>
  <div class="photo" style="left:29px;top:77px;width:269px;height:237px;background:linear-gradient(135deg,#b48a6e,#d9b6a2 55%,#8a6a5a)" role="img" aria-label="Two colleagues reviewing work together at a laptop"></div>
  <svg style="position:absolute;left:312px;top:140px" width="30" height="70" viewBox="0 0 30 70"><path d="M10 2 C-2 22 2 48 18 64" fill="none" stroke="var(--blue)" stroke-width="1.2" stroke-dasharray="3 3"/><path d="M14 60 L20 68 L21 58 Z" fill="var(--blue)"/></svg>
  <div class="outlined-box" style="left:335px;top:81px;width:286px;height:75px;padding:10px 15px">
    <div class="box-heading">Investment Goal</div>
    <ul class="ring-list"><li>Superior risk-adjusted returns while preserving capital in all market environments.</li></ul>
  </div>
  <ul class="ring-list" style="position:absolute;left:351px;top:166px;width:300px">
    <li>Our Approach to Meeting Objectives</li>
    <li>Strategically negotiate private investments in publicly traded companies.</li>
    <li>Offer alternative capital solutions for small and micro-cap public companies with market capitalizations up to $2 billion.</li>
    <li>Employ a specialized strategy for collateralized investments.</li>
    <li>Maintain a well-diversified portfolio through tranching and sub-tranching of investments and milestones.</li>
    <li>Execute investments over a 1- to 4-year horizon, ensuring liquidity opportunities throughout.</li>
  </ul>
  <div class="footer">© 2025. ALL Rights Reserved.</div><div class="page-no">Page 04</div>
</section>

<!-- Investment Strategy -->
<section class="slide col-2 row-2">
  <h2 class="slide-title">Investment Strategy</h2>
  <div class="brand"><i></i>Copperleaf Venture Trust</div>
  <div class="photo-frame" style="left:16px;top:64px;width:184px;height:140px;border-bottom:none"></div>
  <div class="photo-block" style="left:226px;top:250px;width:84px;height:76px"></div>
  <div class="photo" style="left:29px;top:77px;width:269px;height:237px;background:linear-gradient(135deg,#9aa6b2,#e8c441 50%,#5f6670)" role="img" aria-label="Presenter pointing at a chart board during a meeting"></div>
  <div class="outlined-box" style="left:336px;top:59px;width:285px;height:112px;padding:10px 15px">
    <div class="box-heading">CVT Funding Specialization</div>
    <ul class="ring-list"><li>CVT focuses on financing Development Stage, Emerging Growth, and Distressed public companies. This is achieved through a structured approach, wherein investments are tranched over a one- to four-year timeframe.</li></ul>
  </div>
  <div style="position:absolute;left:351px;top:180px;width:260px">
    <div class="box-heading" style="margin-bottom:2px">Objectives:</div>
    <p style="font-size:8.4px;line-height:15px;color:var(--text);margin-bottom:2px">Our strategy serves three key purposes:</p>
    <ul class="ring-list">
      <li style="margin-bottom:6px"><b>Minimize Dilution:</b> Limits the dilution of the issuer's common stock.</li>
      <li style="margin-bottom:6px"><b>Minimize Dilution:</b> Reduces exposure by allowing cessation of further investment in the event of a material adverse change.</li>
      <li><b>Protect Capital:</b> Safeguards against losses stemming from fraud or corporate malfeasance.</li>
    </ul>
  </div>
  <div class="footer">© 2025. ALL Rights Reserved.</div><div class="page-no">Page 05</div>
</section>

<!-- The Organization -->
<section class="slide col-3 row-2">
  <h2 class="slide-title">The Organization</h2>
  <div class="brand"><i></i>Copperleaf Venture Trust</div>
  <div class="outlined-box" style="left:46px;top:104px;width:221px;height:173px;padding:30px 20px">
    <div style="font-size:16px;font-weight:600;margin-bottom:22px">The Organization</div>
    <div style="position:relative;padding-left:16px;font-size:13px;font-weight:500;line-height:19px">
      <span style="position:absolute;left:2px;top:6px;width:6px;height:6px;border:1.5px solid var(--blue);border-radius:50%"></span>
      The Organization CVT's Competitive Advantage: What Sets Us Apart
    </div>
  </div>
  <div class="photo-block" style="left:313px;top:245px;width:84px;height:79px"></div>
  <div class="photo" style="left:324px;top:75px;width:270px;height:237px;background:linear-gradient(135deg,#c8c2ba,#8c8a88 50%,#2d3642)" role="img" aria-label="Two business partners smiling over documents at a desk"></div>
  <div class="footer">© 2025. ALL Rights Reserved.</div><div class="page-no">Page 06</div>
</section>

<!-- Competitive Advantage / Org chart -->
<section class="slide col-1 row-3">
  <h2 class="slide-title">The CVT Organization</h2>
  <div class="brand"><i></i>Copperleaf Venture Trust</div>
  <svg style="position:absolute;left:20px;top:80px" width="222" height="228" viewBox="0 0 222 228">
    <path d="M221 18 V1 H1 V227 H221 V192" fill="none" stroke="var(--blue)" stroke-width="1.5"/>
  </svg>
  <div style="position:absolute;left:65px;top:118px;width:270px">
    <div style="font-size:16.5px;font-weight:600;margin-bottom:8px">CVT's Competitive Advantage</div>
    <ul class="ring-list" style="margin-left:-2px"><li>This Presentation is a summary and does not constitute an offer to sell, or a solicitation of any offer to buy or sell, any securities. Any such offer will be made solely to qualified investors by means of an offering memorandum and related subscription materials, which will contain material information not contained herein. This Presentation is not intended to replace any such offering memorandum.</li></ul>
  </div>
  <div class="chart-head">CVT Investments, LLC</div>
  <svg style="position:absolute;left:370px;top:108px" width="72" height="175" viewBox="0 0 72 175">
    <path d="M20 0 H7 V164" fill="none" stroke="var(--blue)" stroke-width="1" stroke-dasharray="2 2"/>
    <path d="M3 32 L7 40 L11 32 Z" fill="var(--blue)"/>
    <path d="M7 71 H63 M7 117 H63 M7 164 H63" stroke="var(--blue)" stroke-width="1" stroke-dasharray="2 2"/>
    <path d="M62 66 L70 71 L62 76 Z M62 112 L70 117 L62 122 Z M62 159 L70 164 L62 169 Z" fill="var(--blue)"/>
  </svg>
  <div class="chart-member" style="top:160px">Daniel Verhoff – Member</div>
  <div class="chart-member" style="top:206px">Rohan Malik – Member</div>
  <div class="chart-member" style="top:252px">Peter Lindqvist – Member</div>
  <div class="footer">© 2025. ALL Rights Reserved.</div><div class="page-no">Page 07</div>
</section>

<!-- Senior Management -->
<section class="slide col-2 row-3">
  <h2 class="slide-title">Senior Management</h2>
  <div class="brand"><i></i>Copperleaf Venture Trust</div>
  <div class="person-photo" style="top:48px" role="img" aria-label="Black and white portrait of Daniel Verhoff"></div>
  <div class="person" style="top:46px">
    <h3>Daniel Verhoff</h3>
    <ul class="ring-list"><li>Daniel Verhoff is a Founder and Member of CVT Investments LLC, bringing over 17 years of experience in private investment in public equity transactions. Before launching his own funds, he co-founded several investment funds and managed portfolios for a boutique family of funds. He began his career as an analyst at a hedge fund, overseeing more than fifty portfolio companies, and holds a Bachelor of Arts in Finance.</li></ul>
  </div>
  <div class="person-photo" style="top:148px" role="img" aria-label="Black and white portrait of Rohan Malik"></div>
  <div class="person" style="top:146px">
    <h3>Rohan Malik</h3>
    <ul class="ring-list"><li>Rohan Malik is a Founder and Member of CVT Investments LLC with extensive experience investing in publicly traded companies since 2011. He has co-founded multiple investment funds, served at a state agency, a litigation firm and a technology company before moving into finance. He earned his Juris Doctor and holds a Bachelor's degree in Philosophy, Politics, and Law.</li></ul>
  </div>
  <div class="person-photo" style="top:245px" role="img" aria-label="Black and white portrait of Peter Lindqvist"></div>
  <div class="person" style="top:243px">
    <h3>Peter Lindqvist</h3>
    <ul class="ring-list"><li>Peter Lindqvist is a business executive with extensive C-level and Board of Director leadership experience across multiple privately and publicly held companies. He is currently a Founder and Member of CVT Investments LLC. Previously, he was Founder, Chairman, and CEO of Meridian Biobank Corp., a company storing stem cells in the U.S. and internationally, from 2003 to 2012. He also served as CEO of Meridian Partners Inc. and as Founder of Eastbridge Cell Labs.</li></ul>
  </div>
  <div class="footer">© 2025. ALL Rights Reserved.</div><div class="page-no">Page 08</div>
</section>

<!-- Brand panel -->
<div class="brand-panel"><i></i><span>Copperleaf<br>Venture Trust</span></div>

</body>
</html>
```